Community Management Company in need of WordPress templates for website redesign

We are a community association management company providing services to homeowner associations (HOAs), condominium associations, cooperatives, municipal utility districts, luxury high-rises and large master-planned communities within the Real Estate category.

We are looking to do a refresh of our site with newly-designed pages that are compatible with WordPress and can be uploaded to a domain with little complications.

We are interested in first having a landing page designed based on a specific audience and call to actions as described in the design brief file attached to this design project and pasted below:
Design Brief for HavenStead Website Refresh

General Details:
Company Name: HavenStead
Business Location: Carrollton, TX – HQ
Current website: www.havenstead-example.com

Overview:

We are looking to for a refresh of our site with newly-designed pages that are compatible with WordPress and can be uploaded to a domain with little complications.

Our target audience / target market:
HOA and Association Board Members, Real Estate Builders & Developers, Residents and Homeowners, Vendors, Potential Business Partners

Project scope:
Create a landing page template with the target audience of HOA Board Members who are prospects of HavenStead
The goal of the landing page is to have them fill out the proposal form by having the page take them from our “why” message to our “how” and “what” messages so they are compelled to fill out the form. The new landing page needs to drive that behavior.
Our messages will include the following

Why messages:
• Because you deserve an exceptional community
• Because you and your residents deserve an exceptional lifestyle
• Because your community matters
• Because your residents matter
• Exceptional Community. Managed
• Exceptional Lifestyle. Delivered
How/What messages:

With over 25 years of experience, HavenStead provides exceptional community management solutions with the transparency and visibility your community deserves. Our fully integrated services are provided at competitive prices with the best people, best practices, and best cloud-based and mobile app technology.

Our team is made up of the industry’s leading experts equipped to answer your questions quickly. Our team includes: certified managers, degreed and certified accountants, experienced, multi-lingual customer service representatives, technology staff and industry executives. We perform industry leading best practices, on behalf of the communities we serve, ensuring you receive the highest level support, guidance and tools to assist in performing your fiduciary duties. With our proprietary, cloud-based and mobile app technology, pertinent community information is at your fingertips. You will be empowered to manage the business affairs of your community anytime, from any device, anywhere.

Our community management services include personalized onsite management, portfolio management, full-service community maintenance services, community management for builders and property developers, and Virtual CAM (Community Association Manager) management.

Our community communication services include cloud-based board, resident, closing, and attorney portals and mobile app technology, providing the transparency and visibility into the business affairs that your community deserves. In addition, we provide several communication tools to keep homeowners and residents informed via our community website, newsletter and event services.

HavenStead, one of the largest and fastest growing community management companies, is proud to provide exceptional services to hundreds of community associations from under 50 units to over 7,000 units in Arizona, California, Colorado, Florida, Georgia, Louisiana, Nevada, North Carolina, Oregon, Texas and Washington, including homeowner associations (HOAs), condominium associations, cooperatives, luxury high-rises, municipal utility districts and large master-planned communities.

Other page elements: additional content block/placeholders for:
• Link to Service description and technology pages
• Link to Mobile Apps page
• Request a proposal form fill content block
• Find an office form fill content block and link to local page upon completion of search via zip or state
• Contact us content block with information to include phone, email, fax, etc. and link to contact us landing page

Template Elements:
Files will also be uploaded including:
• Logo
• Colors
• Sales PPT for their reference

Please see attached design brief (file #4), logos (file #2&3), colors & branding standards (file #5) and a sales PPT deck (file #1) geared towards the audience for your reference.
Updates

Reason: I am extending the deadline by one week to give everyone a chance to provide updates based on the feedback and submissions. Thank you for all of your efforts. I look forward to seeing all of your designs.

Reason: Good day everyone, We are extending our deadline by one more week; so please continue to submit your designs and revisions. We look forward to seeing your work. Regards.

Thank you for all of your submissions.  I am in the process of getting votes tallied and should have some further information Tuesday of next week.

I am currently reviewing the votes and comments from the poll and will provide feedback within the next day; so please stay tuned.

We are conducting one more round of voting for the website refresh.  Once this is complete we will contact the finalists and make a selection shortly thereafter.  Thank you again for your participation.  Please stay tuned.

We are finalizing our 2nd poll and will request revisions, if appropriate.  Thank you.

Target Market(s)

HOA Board members per the design brief

Industry/Entity Type

Communication

Requirements
Must have
• focus on a landing page first; not the homepage design
Nice to have
• Please see design brief - File #4
Should not have
• home page elements for the time being.

```html
<!DOCTYPE html>
<html lang="en">
<head>
<meta charset="utf-8">
<title>HavenStead – Landing Page</title>
<link href="https://fonts.googleapis.com/css2?family=Open+Sans:wght@400;600&family=Oxygen:wght@400;700&display=swap" rel="stylesheet">
<style>
  :root{
    --page-bg:#fdfdfb;
    --brand-green:#3f6f2a;
    --brand-teal:#1d6777;
    --nav-blue:#0f6f8f;
    --body-text:#555;
    --footer-bg:#f4f4f2;
    --footer-line:#e2e2e0;
    --footer-text:#444;
    --icon-grey:#555;
  }
  *{box-sizing:border-box;margin:0;padding:0}
  html,body{width:1100px;height:1200px;overflow:hidden;background:var(--page-bg)}
  body{font-family:"Open Sans",Arial,sans-serif;color:var(--body-text);position:relative}

  .site-header{height:112px;position:relative;border-bottom:1px solid #e6e6e4}
  .brand{position:absolute;left:99px;top:36px;display:flex;align-items:center;gap:10px}
  .brand-mark{width:18px;height:18px;background:var(--brand-teal)}
  .brand-name{font-family:"Oxygen",Arial,sans-serif;font-weight:700;font-size:34px;color:var(--brand-green);letter-spacing:-.5px}
  .header-phone{position:absolute;right:99px;top:16px;display:flex;align-items:center;gap:4px;font-family:"Oxygen",Arial,sans-serif;font-size:24px;color:var(--brand-green)}
  .main-nav{position:absolute;right:97px;top:68px;display:flex;gap:46px}
  .main-nav a{font-size:16px;color:var(--nav-blue);text-decoration:none;letter-spacing:.2px}

  .hero{position:absolute;top:112px;left:0;width:1100px;height:471px;
    background:
      linear-gradient(180deg,rgba(0,0,0,0) 60%,rgba(60,90,40,.35) 100%),
      linear-gradient(100deg,#7a9a5a 0%,#e9e2d3 18%,#efe9dd 45%,#d6c9b2 60%,#a8d3ec 75%,#9fcde8 100%);}
  .hero-lawn{position:absolute;left:0;right:0;bottom:0;height:150px;
    background:linear-gradient(180deg,rgba(120,150,80,0) 0%,rgba(105,150,60,.75) 60%,rgba(90,130,50,.9) 100%)}
  .hero-copy{position:absolute;left:96px;top:190px;color:#fff;font-family:"Open Sans",Arial,sans-serif;text-shadow:0 1px 3px rgba(0,0,0,.35)}
  .hero-copy .lead{display:block;font-size:37px;line-height:42px}
  .hero-copy .strong{display:block;font-size:51px;line-height:52px}
  .slider-dots{position:absolute;left:526px;bottom:16px;display:flex;gap:3px}
  .slider-dots span{width:14px;height:14px;border-radius:50%;background:#fff;opacity:.9}

  .intro{position:absolute;top:612px;left:98px;width:905px}
  .intro h1{font-family:"Oxygen",Arial,sans-serif;font-weight:400;font-size:33px;color:var(--brand-teal);margin-bottom:8px}
  .intro p{font-size:12px;line-height:19px;margin:0 0 13px 3px}
  .cta-row{display:flex;gap:13px;margin:18px 0 0 3px}
  .btn{width:126px;height:34px;border-radius:3px;color:#fff;font-size:13px;display:flex;align-items:center;justify-content:center;text-decoration:none;text-transform:uppercase}
  .btn-start{background:linear-gradient(#5f8d33,#3c6720)}
  .btn-learn{background:linear-gradient(#1f7687,#0f5261)}

  .site-footer{position:absolute;top:1109px;left:0;width:1100px;height:91px;background:var(--footer-bg);border-top:1px solid var(--footer-line)}
  .footer-nav{position:absolute;left:99px;top:28px;font-size:15px;color:var(--footer-text)}
  .footer-nav a{color:var(--footer-text);text-decoration:none}
  .footer-nav .sep{margin:0 9px}
  .copyright{position:absolute;left:99px;top:62px;font-size:12px;color:#666}
  .social{position:absolute;right:99px;top:26px;display:flex;gap:6px}
  .social span{width:20px;height:20px;border-radius:50%;background:var(--icon-grey)}
</style>
</head>
<body>
  <header class="site-header">
    <div class="brand"><span class="brand-mark"></span><span class="brand-name">HavenStead</span></div>
    <div class="header-phone">
      <svg width="20" height="20" viewBox="0 0 24 24" aria-hidden="true"><path fill="#ccc" d="M6.6 10.8a15 15 0 0 0 6.6 6.6l2.2-2.2c.3-.3.7-.4 1-.2 1.1.4 2.3.6 3.6.6.6 0 1 .4 1 1V20c0 .6-.4 1-1 1A17 17 0 0 1 3 4c0-.6.4-1 1-1h3.5c.6 0 1 .4 1 1 0 1.3.2 2.5.6 3.6.1.3 0 .7-.2 1z"/></svg>
      555.014.0190
    </div>
    <nav class="main-nav">
      <a href="#">HOME</a><a href="#">ABOUT</a><a href="#">FEATURES</a><a href="#">BLOG</a><a href="#">CONTACT</a>
    </nav>
  </header>

  <section class="hero" role="img" aria-label="Photo of a Mediterranean-style white villa with terracotta roof, garden and lawn under a blue sky">
    <div class="hero-lawn"></div>
    <h2 class="hero-copy"><span class="lead">Because you deserve an</span><span class="strong">Exceptional Community</span></h2>
    <div class="slider-dots"><span></span><span></span><span></span></div>
  </section>

  <main class="intro">
    <h1>Welcome to Our Website Mainpage</h1>
    <p>With over 25 years of experience, HavenStead provides exceptional community management solutions with the transparency and visibility your community deserves. Our fully integrated services are provided at competitive prices with the best people, best practices, and best cloudbased and mobile app technology. Our team is made up of the industry’s leading experts equipped to answer your questions quickly.</p>
    <p>Our team includes: certified managers, degreed and certified accountants, experienced, multi lingual customer service representatives, technology staff and industry executives. We perform industry leading best practices, on behalf of the communities we serve, ensuring you receive the highest level support, guidance and tools to assist in performing your fiduciary duties. With our proprietary, cloudbased and mobile app technology, pertinent community information is at your fingertips. You will be empowered to manage the business affairs of your community anytime, from any device, anywhere.</p>
    <p>Our community management services include personalized onsite management, portfolio management, fullservice community maintenance services, community management for builders and property developers, and Virtual CAM (Community Association Manager) management.</p>
    <p>Our community communication services include cloudbased board, resident, closing, and attorney portals and mobile app technology, providing the transparency and visibility into the business affairs that your community deserves. In addition, we provide several communication tools to keep homeowners and residents informed via our community website, newsletter and event services.</p>
    <p>HavenStead, one of the largest and fastest growing community management companies, is proud to provide exceptional services to hundreds of community associations from under 50 units to over 7,000 units in Arizona, California, Colorado, Florida, Georgia, Louisiana, Nevada, North Carolina, Oregon, Texas and Washington, including homeowner associations (HOAs), condominium associations, cooperatives, luxury highrises, municipal utility districts and large masterplanned communities.</p>
    <div class="cta-row">
      <a class="btn btn-start" href="#">Get Started</a>
      <a class="btn btn-learn" href="#">Learn More</a>
    </div>
  </main>

  <footer class="site-footer">
    <nav class="footer-nav">
      <a href="#">Home</a><span class="sep">|</span><a href="#">About</a><span class="sep">|</span><a href="#">Services</a><span class="sep">|</span><a href="#">Support</a><span class="sep">|</span><a href="#">Contact</a>
    </nav>
    <p class="copyright">Copyright © 2014 Company Name.&nbsp; All right reserved</p>
    <div class="social" aria-label="Social links"><span></span><span></span><span></span></div>
  </footer>
</body>
</html>
```